Business Card Design for Varomir Facility Services

We are looking for a Business Card Design for the Company "Varomir Facility Services."
Front side:
- Company Logo (small)
- Company Name, address, pohone, website and personal data.
- white background, for text e.g. company colors (blue or green like in the logo)
Please use following data:
Company data:
Varomir Facility Services Kostelac
Birkenhaldweg 14
6347 Hollwil
www.varomir-fs.ch
Person data:
Tarik Kostelac
Geschäftsführer
+41 76 519 47 83
info@varomir-fs.ch
Back side:
could be colored in blue or green
please use a big logo sing and some smaller icons to say what is all beeing offered in facility services, like cleaning, maintenance cleaning
industrial cleaning, caretaking, gardening, disposal. There is no need for everyone of the icons if there are similar or an icon is standing for more of them.
colors to use:
blue: HEX 246BB0
green: HEX 52B33E

```html
<!DOCTYPE html>
<html lang="de">
<head>
<meta charset="utf-8">
<title>Varomir Facility Services – Visitenkarte</title>
<link rel="stylesheet" href="https://fonts.googleapis.com/css2?family=Lato:wght@400;700&display=swap">
<style>
  :root {
    --stage: #1c1c1e;
    --card: #141415;
    --card-edge: #232325;
    --blue: #246bb0;
    --green: #52b33e;
    --white: #f2f2f2;
    --rule: rgba(255,255,255,0.28);
  }
  * { box-sizing: border-box; margin: 0; padding: 0; }
  html, body { width: 1200px; height: 900px; overflow: hidden; }
  body {
    background: var(--stage);
    font-family: "Lato", Arial, sans-serif;
    display: flex;
    flex-direction: column;
    align-items: center;
    justify-content: center;
    gap: 60px;
  }
  .card {
    position: relative;
    width: 630px;
    height: 360px;
    background: var(--card);
    border: 1px solid var(--card-edge);
    border-radius: 22px;
    box-shadow: 0 14px 40px rgba(0,0,0,0.55);
    overflow: hidden;
  }

  /* Back side */
  .card-back .brand {
    position: absolute;
    top: 78px; left: 0; right: 0;
    display: flex; justify-content: center; align-items: center; gap: 14px;
  }
  .brand-dot {
    width: 18px; height: 18px; border-radius: 50%;
    background: var(--white);
  }
  .card-back .brand-name {
    color: var(--white);
    font-weight: 700;
    font-size: 30px;
    letter-spacing: 3px;
    text-transform: uppercase;
  }
  .card-back .rule {
    position: absolute;
    left: 60px; right: 60px; top: 230px;
    height: 1px; background: var(--rule);
  }
  .services {
    position: absolute;
    top: 250px; left: 0; right: 0;
    text-align: center;
    color: var(--white);
    font-size: 13px;
    letter-spacing: 1px;
    line-height: 1.6;
    text-transform: uppercase;
  }

  /* Front side */
  .card-front .brand {
    position: absolute;
    top: 48px; right: 40px;
    display: flex; align-items: center; gap: 12px;
  }
  .card-front .brand-dot { background: var(--blue); width: 16px; height: 16px; }
  .card-front .brand-name {
    color: var(--blue);
    font-weight: 700;
    font-size: 26px;
    letter-spacing: 2px;
    text-transform: uppercase;
  }
  .card-front .rule {
    position: absolute;
    left: 40px; right: 40px; top: 122px;
    height: 1px; background: var(--rule);
  }
  .person {
    position: absolute;
    left: 44px; bottom: 36px;
  }
  .person-name {
    color: var(--blue);
    font-weight: 700;
    font-size: 21px;
    letter-spacing: 1px;
    text-transform: uppercase;
  }
  .person-role {
    color: var(--green);
    font-size: 16px;
    margin-bottom: 16px;
  }
  .contact-list { list-style: none; }
  .contact-list li {
    display: flex; align-items: center; gap: 10px;
    color: var(--white);
    font-size: 16px;
    line-height: 1.55;
  }
  .contact-list svg { width: 14px; height: 14px; flex: none; }
  .company-address {
    position: absolute;
    right: 44px; top: 150px;
    text-align: right;
    font-style: normal;
    font-size: 16px;
    line-height: 1.3;
  }
  .company-address .company { color: var(--blue); }
  .company-address .street { color: var(--white); }
</style>
</head>
<body>

  <section class="card card-back" aria-label="Rückseite">
    <div class="brand">
      <span class="brand-dot"></span>
      <span class="brand-name">Varomir</span>
    </div>
    <div class="rule"></div>
    <p class="services">
      Cleaning | Maintenance Cleaning | Industrial Cleaning<br>
      Caretaking | Gardening | Disposal
    </p>
  </section>

  <section class="card card-front" aria-label="Vorderseite">
    <div class="brand">
      <span class="brand-dot"></span>
      <span class="brand-name">Varomir Facility Services</span>
    </div>
    <div class="rule"></div>

    <address class="company-address">
      <span class="company">Varomir Facility Services<br>Kostelac</span><br>
      <span class="street">Birkenhaldweg 14<br>6347 Hollwil</span>
    </address>

    <div class="person">
      <p class="person-name">Tarik Kostelac</p>
      <p class="person-role">Geschäftsführer</p>
      <ul class="contact-list">
        <li>
          <svg viewBox="0 0 16 16" aria-hidden="true"><path fill="#246bb0" d="M3.6 1.5l2.3 2.6-1.3 1.6c.9 2 2.6 3.7 4.6 4.6l1.6-1.3 2.6 2.3-1.4 2.2C6.8 13.2 2.8 9.2 1.5 3z"/></svg>
          +41 76 519 47 83
        </li>
        <li>
          <svg viewBox="0 0 16 16" aria-hidden="true"><rect x="1" y="3" width="14" height="10" rx="1" fill="#246bb0"/><path d="M1.5 3.5L8 9l6.5-5.5" fill="none" stroke="#141415" stroke-width="1.3"/></svg>
          info@varomir-fs.ch
        </li>
        <li>
          <svg viewBox="0 0 16 16" aria-hidden="true"><circle cx="8" cy="8" r="7" fill="#246bb0"/><path d="M1.5 8h13M8 1c2.2 2 2.2 12 0 14M8 1c-2.2 2-2.2 12 0 14" fill="none" stroke="#141415" stroke-width="1"/></svg>
          www.varomir-fs.ch
        </li>
      </ul>
    </div>
  </section>

</body>
</html>
```